Profesional personal website needs design and business card

I need a business card with my professional name as a logo "Dorian Vitality" for my business. I am a Wellness Coach, consultant and trainer. So it should be professional, wellness oriented and modern.

Target Market(s)

Private clients, governments, corporations. Luxury and high market.

Industry/Entity Type

Health And Wellness

Contact Information for Business Card

Dorian Vitality should be the logo

Colors

Designer to choose colors to be used in the design.

Requirements
Must have
• Dorian Vitality
• Name: Tomás Lirandel
• Wellness Coach, Consultant & Trainer.
• Website: www.dorianvitality-example.com
• Phone:
• Spain (+34) 612 480 317
• (USA) +1 (555) 610 4829
Nice to have
• The most important is the design of "Dorian Vitality", as this is going to be my personal brand logo. It should be professional, wellness, high end and actual.
Should not have
• no golds, no baroque style..

```html
<!DOCTYPE html>
<html lang="en">
<head>
<meta charset="utf-8">
<title>Dorian Vitality – Business Card</title>
<link rel="stylesheet" href="https://fonts.googleapis.com/css2?family=Montserrat:wght@600&family=Poppins:wght@500&family=Roboto:wght@400&family=Roboto+Condensed:wght@700&display=swap">
<style>
  :root {
    --page: #ffffff;
    --card: #ffffff;
    --lime: #e6eb9c;
    --sand: #c7a386;
    --sand-soft: rgba(184, 147, 116, 0.55);
    --peach: #fdd391;
    --brand-ink: #0f2c33;
    --name-brown: #874d22;
    --rule-brown: #a9774f;
    --text: #111111;
    --phone-badge: #d4e02b;
  }
  * { margin: 0; padding: 0; box-sizing: border-box; }
  html, body {
    width: 1000px; height: 1200px; overflow: hidden;
    background: var(--page);
  }
  .sheet { position: relative; width: 1000px; height: 1200px; }
  .card {
    position: absolute; left: 81px;
    width: 848px; height: 484px;
    background: var(--card);
    overflow: hidden;
  }
  .card--front { top: 74px; }
  .card--back  { top: 632px; }

  .card__backdrop {
    position: absolute; inset: 0;
    background:
      radial-gradient(ellipse 50% 56% at 52% 50%, rgba(255,255,255,1) 72%, rgba(255,255,255,0) 100%),
      radial-gradient(ellipse 62% 70% at 52% 50%, rgba(255,255,255,0) 60%, var(--sand-soft) 100%),
      linear-gradient(135deg, var(--lime) 0%, #ffffff 38%, #ffffff 62%, var(--peach) 100%);
  }

  .brand-name {
    position: absolute; left: 0; right: 0; top: 268px;
    text-align: center;
    font-family: "Montserrat", sans-serif; font-weight: 600;
    font-size: 46px; letter-spacing: 3px;
    color: var(--brand-ink);
  }
  .website {
    position: absolute; left: 0; right: 0; top: 400px;
    text-align: center;
    font-family: "Roboto", sans-serif; font-size: 20px;
    color: var(--text);
  }

  .person-name {
    position: absolute; left: 276px; width: 324px; top: 136px;
    text-align: center;
    font-family: "Roboto Condensed", sans-serif; font-weight: 700;
    font-size: 48px; line-height: 1; letter-spacing: -0.5px;
    color: var(--name-brown);
  }
  .person-role {
    position: absolute; left: 256px; width: 364px; top: 188px;
    text-align: center;
    font-family: "Poppins", sans-serif; font-weight: 500;
    font-size: 15px; color: var(--text);
  }
  .rule { position: absolute; height: 3px; background: var(--rule-brown); }
  .rule--one   { left: 286px; top: 230px; width: 237px; }
  .rule--two   { left: 351px; top: 244px; width: 238px; }
  .rule--three { left: 286px; top: 257px; width: 237px; }

  .phone-badge {
    position: absolute; left: 282px; top: 326px;
    width: 43px; height: 43px; border-radius: 50%;
    background: var(--phone-badge);
    display: flex; align-items: center; justify-content: center;
  }
  .phone-badge svg { width: 24px; height: 24px; }
  .phone-list {
    position: absolute; left: 351px; top: 320px;
    font-family: "Roboto", sans-serif; font-size: 19px; line-height: 25px;
    color: var(--text);
  }
  .phone-list__row { display: flex; }
  .phone-list__country { width: 60px; }
</style>
</head>
<body>
<div class="sheet">

  <section class="card card--front">
    <div class="card__backdrop" role="img" aria-label="Decorative sweeping curves in lime, sand and peach framing the card"></div>
    <h1 class="brand-name">Dorian Vitality</h1>
    <p class="website">www.dorianvitality-example.com</p>
  </section>

  <section class="card card--back">
    <div class="card__backdrop" role="img" aria-label="Decorative sweeping curves in lime, sand and peach framing the card"></div>
    <h2 class="person-name">Tomás Lirandel</h2>
    <p class="person-role">Wellness Coach, Consultant &amp; Trainer</p>
    <span class="rule rule--one"></span>
    <span class="rule rule--two"></span>
    <span class="rule rule--three"></span>

    <div class="phone-badge">
      <svg viewBox="0 0 24 24" aria-hidden="true">
        <path fill="#111" d="M6.6 2.5c.5-.3 1.1-.2 1.4.3l2.2 3.3c.3.5.2 1.1-.2 1.4L8.6 8.6c.9 2.4 3.4 4.9 5.8 5.8l1.1-1.4c.3-.4.9-.5 1.4-.2l3.3 2.2c.5.3.6.9.3 1.4l-1.2 2c-.5.8-1.5 1.2-2.4.9C11 17.6 6.4 13 4.8 7.2c-.3-.9.1-1.9.9-2.4z"/>
      </svg>
    </div>
    <div class="phone-list">
      <p class="phone-list__row"><span class="phone-list__country">Spain</span><span>: (+34) 612 480 317</span></p>
      <p class="phone-list__row"><span class="phone-list__country">USA</span><span>: +1 (555) 610 4829</span></p>
    </div>
  </section>

</div>
</body>
</html>
```